Luxury WordPress Website for CORALBASINS

I need a professional WordPress website for Coral Basins. The site should be modern, visually appealing, and user-friendly, reflecting the brand’s luxury and premium identity. It must include a homepage, product/service pages, contact form, and be responsive on both desktop and mobile devices. The design should allow for easy updates and integration of future content, while maintaining a polished and professional look.

Target Market(s)

swimmingpool & spa

Industry/Entity Type

Swimmingpool

Coding

Coded - Design and coding required

Font styles to use
Other font styles liked:
• HaboroSoft

Requirements
Must have
• Exclusive appearance
Nice to have
• • A logo that subtly incorporates water or pool elements. • A color palette that reflects luxury, elegance, and relaxation. • Clean and modern typography that is easy to read across all media. • Iconography or design elements that convey premium quality. • A versatile design that can be adapted for social media, merchandise, and promotional materials. • Optional: A tagline that emphasizes luxury and high-end pool experiences.

```html
<!DOCTYPE html>
<html lang="en">
<head>
<meta charset="utf-8">
<title>Coral Basins — Luxury Pools</title>
<link rel="stylesheet" href="https://fonts.googleapis.com/css2?family=Poppins:wght@400;500;600;700&display=swap">
<style>
:root{
  --blue:#1a73e8;
  --blue-bright:#1e88ff;
  --blue-deep:#0d4fb8;
  --ink:#1c1c1c;
  --text:#3a3a3a;
  --muted:#6b6b6b;
  --white:#ffffff;
  --footer:#232323;
  --leaf:#3f8f3a;
  --lime:#c9df7a;
  --coral:#e0584b;
}
*{margin:0;padding:0;box-sizing:border-box}
html,body{width:1200px;height:4511px;overflow:hidden;background:var(--white)}
body{font-family:"Poppins",sans-serif;color:var(--text)}
.page{position:relative;width:1200px;height:4511px;overflow:hidden}
.abs{position:absolute}
.btn-dark{position:absolute;display:flex;align-items:center;justify-content:center;background:var(--ink);color:var(--white);font-size:15px;font-weight:500;border-radius:0 22px 0 22px}
.btn-light{position:absolute;display:flex;align-items:center;justify-content:center;background:var(--white);color:var(--ink);font-size:15px;font-weight:500;border-radius:0 22px 0 22px}
.eyebrow{position:absolute;font-size:13px;font-weight:600;color:var(--ink);letter-spacing:.3px;text-transform:uppercase}
.title-blue{position:absolute;color:var(--blue-bright);font-weight:600;font-size:36px;letter-spacing:.5px;line-height:1.2}
.deco{position:absolute;border-radius:50%}

/* hero */
.hero{position:absolute;left:0;top:0;width:1200px;height:727px;background:linear-gradient(180deg,#4d5a4a 0%,#7d8c86 28%,#5e7f8c 48%,#2f6f86 65%,#1d4a5c 100%)}
.nav{position:absolute;left:240px;top:38px;width:798px;height:44px;background:var(--blue-bright);border-radius:0 22px 0 22px;display:flex;justify-content:flex-end;align-items:center;gap:38px;padding-right:56px}
.nav a{color:var(--white);text-decoration:none;font-size:14px;font-weight:500}
.logo{position:absolute;display:flex;align-items:center;gap:8px;color:var(--white);font-weight:600;z-index:2}
.logo .mark{width:18px;height:18px;border-radius:50%;background:var(--white);flex:none}
.hero-logo{left:160px;top:22px;width:150px;height:86px;background:var(--blue-deep);border-radius:50% 40% 50% 45%;justify-content:center;font-size:14px}
.hero-title{position:absolute;left:0;width:1200px;top:190px;text-align:center;color:var(--white);font-size:36px;font-weight:600;line-height:45px;text-transform:uppercase}
.hero-sub{position:absolute;left:0;width:1200px;top:292px;text-align:center;color:var(--white);font-size:20px;line-height:26px;font-weight:400}
.dots{position:absolute;display:flex;gap:10px}
.dots span{width:10px;height:10px;border-radius:50%;background:var(--blue-bright)}
.dots span.on{background:var(--white)}

/* services */
.card{position:absolute;background:var(--white);border-radius:14px}
.card.raised{box-shadow:0 6px 22px rgba(0,0,0,.12)}
.card .photo{position:absolute;left:0;top:0;width:100%;height:192px;border-radius:14px 0 14px 0}
.card h3{position:absolute;left:20px;top:212px;font-size:16px;font-weight:500;color:var(--ink)}
.card p{position:absolute;left:20px;right:14px;top:244px;font-size:10px;line-height:14px;color:var(--text)}
.card .link{position:absolute;left:20px;top:308px;font-size:10.5px;font-weight:600;color:var(--ink)}
.dots-outline span{background:var(--blue-bright)}
.dots-outline span.on{background:var(--white);border:2px solid var(--blue-bright)}

/* why */
.why-body{position:absolute;left:174px;top:1522px;width:390px;font-size:11.5px;line-height:19px;color:var(--text)}
.feature{position:absolute;left:174px;display:flex;gap:14px;align-items:center}
.feature .icon{width:42px;height:42px;border-radius:50%;border:2px solid var(--blue-bright);display:flex;align-items:center;justify-content:center}
.feature h4{font-size:12px;font-weight:600;color:var(--ink)}
.feature span{font-size:11.5px;color:var(--muted)}

/* banner */
.banner{position:absolute;left:0;top:1936px;width:1200px;height:640px;background:linear-gradient(180deg,#4f8fe0 0%,#7aa8de 20%,#6e8c7c 40%,#5fa9bf 58%,#3fb4d6 75%,#2a9dc7 100%)}
.banner h2{position:absolute;left:0;width:1200px;top:100px;text-align:center;color:var(--white);font-size:36px;font-weight:600;line-height:46px;text-transform:uppercase}

/* products */
.product{position:absolute;top:2716px;height:338px}
.product.center{border-radius:0 0 0 36px}
.product .caption{position:absolute;left:0;right:0;bottom:0;height:80px;border-radius:0 0 0 36px;background:linear-gradient(180deg,rgba(30,136,255,0),rgba(30,136,255,.95));display:flex;align-items:flex-end;justify-content:center;padding-bottom:22px;color:var(--white);font-size:13.5px;font-weight:600;text-transform:uppercase}

/* testimonials */
.testi{position:absolute;left:0;top:3218px;width:1200px;height:460px;background:linear-gradient(180deg,#2f7fe0,#3b8ce6 60%,#4a96ea)}
.testi h2{position:absolute;left:0;width:1200px;top:44px;text-align:center;color:var(--white);font-size:34px;font-weight:600}
.quote{position:absolute;left:326px;top:116px;width:547px;height:170px;background:#114c98;border-radius:0 36px 0 36px}
.quote .avatar{position:absolute;left:34px;top:36px;width:78px;height:78px;border-radius:50%;background:linear-gradient(135deg,#d9dfe6,#b9c6d4);border:3px solid var(--white)}
.quote p{position:absolute;left:142px;top:40px;width:380px;color:var(--white);font-size:15px;line-height:19px}
.quote strong{position:absolute;left:142px;top:104px;color:var(--white);font-size:15px;font-weight:600}
.arrow{position:absolute;top:182px;color:var(--white);font-size:26px;font-weight:400}

/* contact */
.contact{position:absolute;left:0;top:3600px;width:1200px;height:548px;background:linear-gradient(180deg,#eef4fb,#f6f9fd 50%,#e9eff6)}
.field{position:absolute;background:var(--white);border:1px solid #5a8fd9;border-radius:0 14px 0 14px;font-size:11px;color:var(--ink);padding:14px 14px}

/* footer */
.footer{position:absolute;left:0;top:4147px;width:1200px;height:364px;background:var(--footer);color:var(--white)}
.footer h5{position:absolute;top:58px;font-size:15px;font-weight:600}
.f-line{position:absolute;font-size:11.5px;line-height:16px;display:flex;gap:10px;align-items:flex-start}
.f-link{position:absolute;left:368px;font-size:11.5px;display:flex;gap:12px}
.newsletter{position:absolute;left:555px;top:100px;width:198px;height:28px;background:var(--white);border-radius:0 10px 0 10px;font-size:10px;color:var(--ink);padding:7px 12px}
.social{position:absolute;top:172px;width:34px;height:34px;border-radius:50%;background:var(--blue-bright);border:2px solid var(--white)}
.copy{position:absolute;left:0;width:1200px;top:4474px;text-align:center;color:var(--white);font-size:10px}
</style>
</head>
<body>
<div class="page">

  <!-- HERO -->
  <section class="hero" role="img" aria-label="Infinity pool at a tropical resort with palm trees and loungers at sunset"></section>
  <nav class="nav">
    <a>Home</a><a>About Us</a><a>Services</a><a>Product</a><a>Contact Us</a>
  </nav>
  <div class="logo hero-logo"><span class="mark"></span>Coral Basins</div>
  <h1 class="hero-title">Elevate your lifestyle with<br>Coral Basins</h1>
  <p class="hero-sub">Experience the art of luxury pool design, where<br>innovation meets elegance.</p>
  <div class="btn-dark" style="left:380px;top:368px;width:200px;height:47px">Explore Our Pools</div>
  <div class="btn-light" style="left:594px;top:368px;width:226px;height:47px">Request a Consultation</div>
  <div class="dots" style="left:594px;top:545px"><span></span><span class="on"></span><span></span><span></span></div>
  <svg class="abs" style="left:0;top:560px" width="1200" height="170" viewBox="0 0 1200 170">
    <path d="M0 170 L0 150 C150 100 260 60 420 80 C600 105 700 150 880 130 C1020 115 1120 70 1200 60 L1200 170 Z" fill="#fff"/>
    <path d="M0 150 C150 100 260 60 420 80 C600 105 700 150 880 130 C1020 115 1120 70 1200 60" fill="none" stroke="#1e88ff" stroke-width="14"/>
    <path d="M300 95 C450 70 560 110 700 122" fill="none" stroke="#1e88ff" stroke-width="6"/>
  </svg>
  <div class="deco" role="img" aria-label="Beach ball" style="left:180px;top:600px;width:118px;height:118px;background:#8ec4dc"></div>

  <!-- SERVICES -->
  <div class="eyebrow" style="left:0;width:1200px;text-align:center;top:763px">Discover your perfect pool</div>
  <div class="title-blue" style="left:0;width:1200px;text-align:center;top:780px">SERVICES</div>

  <div class="card" style="left:166px;top:858px;width:267px;height:360px">
    <div class="photo" role="img" aria-label="Lush garden wellness pool and spa seen from above" style="background:linear-gradient(135deg,#1f3b2a,#3e6e57 50%,#2b4a34)"></div>
    <h3>Wellness Series</h3>
    <p>Designed for tranquility and health. Perfectly balanced between form and function, these pools and spas nurture body and mind.</p>
    <div class="link">Explore Wellness Options</div>
  </div>
  <div class="card raised" style="left:459px;top:850px;width:282px;height:376px">
    <div class="photo" role="img" aria-label="Modern white house with a blue backyard pool" style="left:8px;top:8px;width:266px;background:linear-gradient(180deg,#cfd8df,#e8ecef 45%,#3aa3d8 75%,#1b7fc4)"></div>
    <h3 style="left:24px;top:220px">Architectural Series</h3>
    <p style="left:24px;top:252px">Bold, modern, and artfully engineered — for homes that embrace design excellence.</p>
    <div class="link" style="left:24px;top:314px">View Design Inspirations</div>
  </div>
  <div class="card" style="left:771px;top:858px;width:267px;height:360px">
    <div class="photo" role="img" aria-label="Resort pool with loungers at dusk" style="background:linear-gradient(180deg,#6d5a4c,#8e7a6a 45%,#2e6f9e 70%,#1c4f7a)"></div>
    <h3>Resort Series</h3>
    <p>Transform your property into a luxury retreat. Our Resort Series pools deliver an unmatched blend of leisure and beauty.</p>
    <div class="link">Request a Consultation</div>
  </div>
  <div class="dots dots-outline" style="left:557px;top:1283px"><span></span><span class="on"></span><span></span><span></span><span></span></div>
  <div class="deco" role="img" aria-label="Tropical leaf" style="left:122px;top:1200px;width:116px;height:100px;background:var(--leaf);border-radius:50% 50% 50% 10%"></div>
  <div class="deco" style="left:258px;top:1230px;width:18px;height:18px;background:var(--lime)"></div>
  <div class="deco" style="left:92px;top:1284px;width:14px;height:14px;background:var(--coral)"></div>
  <div class="deco" role="img" aria-label="Coconut drink" style="left:1012px;top:1168px;width:112px;height:112px;background:#6b4124"></div>
  <div class="deco" style="left:975px;top:1218px;width:14px;height:14px;background:var(--lime)"></div>

  <!-- WHY -->
  <div class="eyebrow" style="left:174px;top:1414px">Why Coral Basins</div>
  <div class="title-blue" style="left:174px;top:1432px;line-height:44px">CRAFTING THE WORLD’S<br>FINEST POOLS</div>
  <div class="why-body">Coral Basins creates exclusive, custom-designed swimming pools for clients who expect nothing less than perfection.<br>From minimalist architectural marvels to resort-style sanctuaries, each Coral Basins pool is built with precision, passion, and performance in mind.</div>
  <div class="feature" style="top:1630px">
    <div class="icon"><svg width="22" height="22" viewBox="0 0 22 22" fill="none" stroke="#1e88ff" stroke-width="1.6"><circle cx="11" cy="11" r="4"/><path d="M11 2v4M11 16v4M2 11h4M16 11h4M4.5 4.5l2.8 2.8M14.7 14.7l2.8 2.8M4.5 17.5l2.8-2.8M14.7 7.3l2.8-2.8"/></svg></div>
    <div><h4>Masterful Engineering</h4><span>Designed to last a lifetime.</span></div>
  </div>
  <div class="feature" style="top:1688px">
    <div class="icon"><svg width="22" height="22" viewBox="0 0 22 22" fill="none" stroke="#1e88ff" stroke-width="1.6"><path d="M2 8c3-3 6 3 9 0s6 3 9 0M2 13c3-3 6 3 9 0s6 3 9 0M2 18c3-3 6 3 9 0s6 3 9 0"/></svg></div>
    <div><h4>Premium Materials</h4><span>Only the finest finishes and technologies.</span></div>
  </div>
  <div class="feature" style="top:1742px">
    <div class="icon"><svg width="22" height="22" viewBox="0 0 22 22" fill="none" stroke="#1e88ff" stroke-width="1.6"><path d="M4 18V8l7-5 7 5v10M2 18h18M8 18v-5h6v5"/></svg></div>
    <div><h4>Timeless Design</h4><span>Blending luxury with harmony and nature.</span></div>
  </div>
  <div class="btn-dark" style="left:182px;top:1805px;width:132px;height:44px">Learn More</div>
  <div class="deco" role="img" aria-label="Couple relaxing at the edge of a pool" style="left:627px;top:1408px;width:416px;height:416px;background:linear-gradient(160deg,#6d8c5e,#a7b49a 40%,#3aa6c9 75%,#1d86b4);border:8px solid var(--blue-bright)"></div>
  <div class="deco" role="img" aria-label="Beach ball" style="left:908px;top:1412px;width:86px;height:86px;background:#8ec4dc"></div>
  <div class="deco" role="img" aria-label="Tropical leaf" style="left:640px;top:1736px;width:116px;height:100px;background:var(--leaf);border-radius:50% 50% 50% 10%"></div>
  <div class="deco" style="left:600px;top:1768px;width:18px;height:18px;background:var(--lime)"></div>
  <div class="deco" style="left:768px;top:1822px;width:14px;height:14px;background:var(--coral)"></div>
  <div class="deco" role="img" aria-label="Watermelon swim ring" style="left:22px;top:1822px;width:118px;height:82px;background:#e8645a"></div>
  <div class="deco" role="img" aria-label="Striped deck chair" style="left:930px;top:1800px;width:240px;height:200px;background:#9fd0e0;border-radius:18px"></div>

  <!-- BANNER -->
  <section class="banner" role="img" aria-label="Woman relaxing on a lounger beside an infinity pool overlooking mountains">
    <h2>Begin your journey toward<br>ultimate relaxation and beauty.</h2>
  </section>
  <div class="btn-dark" style="left:481px;top:2144px;width:238px;height:46px">Book a Private Consultation</div>
  <svg class="abs" style="left:0;top:2460px" width="1200" height="130" viewBox="0 0 1200 130">
    <path d="M0 130 L0 110 C200 40 420 30 620 70 C820 110 1000 100 1200 30 L1200 130 Z" fill="#fff"/>
    <path d="M0 110 C200 40 420 30 620 70 C820 110 1000 100 1200 30" fill="none" stroke="#1e88ff" stroke-width="12"/>
    <path d="M260 55 C420 40 560 70 700 92" fill="none" stroke="#1e88ff" stroke-width="5"/>
  </svg>
  <div class="deco" role="img" aria-label="Coconut drink" style="left:893px;top:2520px;width:112px;height:112px;background:#6b4124"></div>

  <!-- PRODUCTS -->
  <div class="deco" role="img" aria-label="Tropical leaf" style="left:275px;top:2594px;width:116px;height:100px;background:var(--leaf);border-radius:50% 50% 50% 10%"></div>
  <div class="deco" style="left:412px;top:2624px;width:18px;height:18px;background:var(--lime)"></div>
  <div class="deco" style="left:248px;top:2680px;width:14px;height:14px;background:var(--coral)"></div>
  <div class="eyebrow" style="left:0;width:1200px;text-align:center;top:2616px">Our signature collections</div>
  <div class="title-blue" style="left:0;width:1200px;text-align:center;top:2633px">PRODUCTS</div>
  <div class="product" role="img" aria-label="Modern house with lit pool and fountains at dusk" style="left:0;width:345px;border-radius:0 0 36px 0;background:linear-gradient(180deg,#9a7a86,#4d4a48 45%,#3fa3c6 75%,#2b8db3)"></div>
  <div class="product center" role="img" aria-label="Resort pool with white parasol and terrace" style="left:371px;width:456px;background:linear-gradient(180deg,#3b8fe2,#dfe6ea 40%,#8fb28a 60%,#3aa6d6)">
    <div class="caption">Resort Series - Your private paradise at home.</div>
  </div>
  <div class="product" role="img" aria-label="Backyard pool with stone deck and planter" style="left:850px;width:350px;border-radius:0 0 0 36px;background:linear-gradient(180deg,#5e8a4e,#3c9fd9 35%,#cfc3b0 65%,#8c7f6e)"></div>
  <div class="btn-dark" style="left:481px;top:3087px;width:238px;height:48px">Explore Our Products</div>
  <div class="deco" role="img" aria-label="Watermelon swim ring" style="left:790px;top:3100px;width:118px;height:82px;background:#e8645a"></div>

  <!-- TESTIMONIALS -->
  <section class="testi" role="img" aria-label="Aerial view of a blue pool">
    <h2>TESTIMONIALS</h2>
    <div class="arrow" style="left:262px">‹</div>
    <div class="arrow" style="left:916px">›</div>
  </section>
  <div class="quote" style="top:3334px">
    <div class="avatar" role="img" aria-label="Client portrait"></div>
    <p>“Our Coral Basins pool completely transformed our home — an architectural masterpiece.”</p>
    <strong>The Alvarez Family</strong>
  </div>

  <!-- CONTACT -->
  <section class="contact"></section>
  <svg class="abs" style="left:0;top:3560px" width="1200" height="110" viewBox="0 0 1200 110">
    <path d="M0 0 L1200 0 L1200 20 C1000 70 820 80 620 60 C420 40 200 60 0 100 Z" fill="#4a96ea"/>
    <path d="M0 100 C200 60 420 40 620 60 C820 80 1000 70 1200 20" fill="none" stroke="#1e88ff" stroke-width="12"/>
    <path d="M300 58 C460 42 600 60 760 72" fill="none" stroke="#1e88ff" stroke-width="5"/>
  </svg>
  <div class="deco" role="img" aria-label="Beach ball" style="left:190px;top:3555px;width:118px;height:118px;background:#8ec4dc"></div>
  <div class="title-blue" style="left:0;width:1200px;text-align:center;top:3700px">CONTACT US</div>
  <div class="field" style="left:300px;top:3775px;width:292px;height:44px">NAME</div>
  <div class="field" style="left:606px;top:3775px;width:293px;height:44px">EMAIL</div>
  <div class="field" style="left:300px;top:3833px;width:292px;height:44px">PHONE</div>
  <div class="field" style="left:606px;top:3833px;width:293px;height:44px">SERVICE</div>
  <div class="field" style="left:300px;top:3889px;width:599px;height:110px">MESSAGE</div>
  <div class="btn-dark" style="left:518px;top:4017px;width:164px;height:45px">Submit</div>
  <div class="deco" role="img" aria-label="Tropical leaf" style="left:205px;top:4070px;width:116px;height:80px;background:var(--leaf);border-radius:50% 50% 10% 10%"></div>
  <div class="deco" style="left:340px;top:4092px;width:18px;height:18px;background:var(--lime)"></div>
  <div class="deco" role="img" aria-label="Striped deck chair" style="left:850px;top:4010px;width:240px;height:190px;background:#9fd0e0;border-radius:18px"></div>

  <!-- FOOTER -->
  <footer class="footer">
    <h5 style="left:161px">Contact Us</h5>
    <h5 style="left:368px">Quick Links</h5>
    <h5 style="left:555px">Newsletter</h5>
    <div class="f-line" style="left:161px;top:100px"><svg width="12" height="16" viewBox="0 0 12 16"><path d="M6 0a6 6 0 0 0-6 6c0 4.5 6 10 6 10s6-5.5 6-10a6 6 0 0 0-6-6z" fill="#1e88ff"/><circle cx="6" cy="6" r="2.2" fill="#232323"/></svg><span>48 Lagoon Avenue,<br>Naples, FL</span></div>
    <div class="f-line" style="left:161px;top:136px"><svg width="14" height="14" viewBox="0 0 14 14"><path d="M3 1l2.5 3-1.5 1.5a8 8 0 0 0 4.5 4.5L10 8.5l3 2.5-1.5 2.5C6 13 1 8 0.5 2.5z" fill="#1e88ff"/></svg><span>+1 (800) 555-0148</span></div>
    <div class="f-line" style="left:161px;top:182px"><svg width="14" height="11" viewBox="0 0 14 11"><rect width="14" height="11" rx="1.5" fill="#1e88ff"/><path d="M1 1.5l6 4.5 6-4.5" stroke="#232323" stroke-width="1.3" fill="none"/></svg><span>hello@coralbasins.com</span></div>
    <div class="f-link" style="top:96px"><span>›</span><span>Home</span></div>
    <div class="f-link" style="top:115px"><span>›</span><span>About Us</span></div>
    <div class="f-link" style="top:134px"><span>›</span><span>Services</span></div>
    <div class="f-link" style="top:153px"><span>›</span><span>Products</span></div>
    <div class="f-link" style="top:172px"><span>›</span><span>Contact Us</span></div>
    <div class="newsletter">Enter Your email</div>
    <svg class="abs" style="left:727px;top:108px" width="12" height="12" viewBox="0 0 12 12"><path d="M0 5l12-5-5 12-1.5-5.5z" fill="#232323"/></svg>
    <div class="social" style="left:555px"></div>
    <div class="social" style="left:598px"></div>
    <div class="social" style="left:641px"></div>
    <div class="social" style="left:684px"></div>
    <div class="logo" style="left:832px;top:72px;width:146px;height:82px;background:var(--blue-deep);border-radius:50% 40% 50% 45%;justify-content:center;font-size:14px"><span class="mark"></span>Coral Basins</div>
    <div class="abs" style="left:125px;top:310px;width:950px;height:1px;background:#3a3a3a"></div>
    <div class="deco" style="left:1034px;top:314px;width:28px;height:28px;background:#25b340"></div>
  </footer>
  <div class="copy">© 2025 • www.coralbasins.com • All Rights Reserved | Privacy Policy &amp; Terms of use</div>

</div>
</body>
</html>
```